New Payments Start-up requires Logo, Style Guide and Web Site Design

We need a logo, style guide (colour templates etc.) and marketing web-site (HTML/CSS styling) for Fenwu, a new account-to-account payment product for use in the Single European Payment Area (SEPA).

The design is for the product only, not a company brand. We're looking for basic palette and style guidelines also. The web site need only be a basic responsive cross-platform design and layout. We will produce our own content.

We have no requirements for specific colours or logo styles. It is a financial product, however, so should not appear too quirky or untrustworthy.

The product is still in the early phases of development, so we're not able to provide pictures or other content.

As a little more detail on how things work, though, our end customers will arrive at our site through redirection from our merchant partners (a number of whom are large multi-national companies) who have offered our services as an alternative to credit card payments. They will be able to set up a SEPA direct debit mandate online in just a few pages, secure that with a password and use it to pay both immediately and in future with a simple confirmation of the password… a quick, easy checkout.

Because we work with large customer in the payments space, whilst we’d like the brand to be modern and appealing, it has to engender trust and stability. Whilst this product is new and in start-up phase, our company has been in alternative payments for nearly 10 years and have strong products in Europe in the Pre-Paid Zelo/TrevinCard and Voucher space. We'd like to treat this separately, however, which is why we've briefed accordingly.

Reason: Apologies for the extension, but I had a couple of designers contact me to say they had completed work but were unable to submit because time ran out. I'll only extend this once, though, because we need to get cracking on the project. Many thanks Jem

Target Market(s)

European alternative payment customers

Industry/Entity Type

Financial

Logo Text

fenwu

Coding

Coded - Design and coding required

Number of Pages Required

1 page

Font styles to use
Sans Serif

```html
<!DOCTYPE html>
<html lang="en">
<head>
<meta charset="utf-8">
<title>Fenwu – Account-to-Account Payments</title>
<link rel="stylesheet" href="https://fonts.googleapis.com/css2?family=Open+Sans:wght@400;600;700&display=swap">
<style>
:root{
  --blue-light:#4fa3dd;
  --blue-mid:#3d8fd1;
  --blue-dark:#2a6cb5;
  --blue-deep:#1f5c9f;
  --ink:#333b44;
  --muted:#8a8f95;
  --rule:#e3e6ea;
  --paper:#ffffff;
  --mist:#f3f4f6;
}
*{box-sizing:border-box;margin:0;padding:0}
html,body{width:1200px;height:2281px;overflow:hidden}
body{font-family:"Open Sans",Arial,sans-serif;color:var(--ink);background:var(--paper);position:relative}
.abs{position:absolute}
a{color:inherit;text-decoration:none}

/* header */
.site-header{position:absolute;left:0;top:0;width:1200px;height:91px;background:var(--paper);border-top:3px solid var(--blue-light);box-shadow:0 1px 3px rgba(0,0,0,.08);z-index:2}
.brand{position:absolute;left:161px;top:30px;display:flex;align-items:center;gap:8px;font-size:30px;font-weight:700;color:var(--blue-dark);letter-spacing:.5px}
.brand-dot{width:16px;height:16px;border-radius:50%;background:var(--blue-light)}
.main-nav a{position:absolute;top:41px;font-size:12px;color:var(--ink);text-transform:uppercase}
.main-nav a.is-active{color:var(--blue-light)}
.nav-caret{position:absolute;left:484px;top:80px;width:0;height:0;border-left:7px solid transparent;border-right:7px solid transparent;border-bottom:7px solid var(--blue-light)}
.btn-nav{position:absolute;top:33px;height:31px;color:#fff;font-size:11px;font-weight:700;display:flex;align-items:center;justify-content:center}
.btn-login{left:910px;width:57px;background:var(--blue-light)}
.btn-signup{left:976px;width:61px;background:var(--blue-dark)}

/* hero */
.hero{position:absolute;left:0;top:91px;width:1200px;height:461px;background:linear-gradient(90deg,#f1f2f3 0%,#eef0f2 40%,#e3e6e9 100%)}
.hero-photo{position:absolute;left:500px;top:0;width:700px;height:461px;background:linear-gradient(100deg,rgba(240,241,242,0) 0%,#d9d5cf 35%,#c9b9a8 60%,#e7e4df 100%)}
.hero-title{position:absolute;left:161px;top:120px;font-size:35px;line-height:42px;font-weight:400;color:var(--blue-light)}
.hero-title strong{font-weight:400;color:var(--blue-deep)}
.hero-text{position:absolute;left:161px;top:222px;width:430px;font-size:15px;line-height:24px;color:#666b70}
.btn-primary{position:absolute;background:var(--blue-dark);color:#fff;font-size:12px;text-transform:uppercase;display:flex;align-items:center;justify-content:center}
.hero .btn-primary{left:161px;top:298px;width:190px;height:35px}
.slider-arrow{position:absolute;top:214px;width:32px;height:32px;border:1px solid #b9bdc2;border-radius:50%}

/* welcome */
.welcome{position:absolute;left:0;top:552px;width:1200px;height:362px;background:var(--paper);overflow:hidden}
.welcome-shade{position:absolute;left:0;top:0}
.welcome-illustration{position:absolute;left:175px;top:41px;width:335px;height:282px;background:radial-gradient(ellipse at 50% 50%,#9fb6c9 0%,#d8dde2 55%,rgba(255,255,255,0) 75%)}
.section-heading{font-size:23px;font-weight:400;color:var(--blue-mid);text-transform:uppercase}
.section-heading strong{font-weight:600;color:var(--blue-deep)}
.welcome .section-heading{position:absolute;left:625px;top:48px}
.lead{position:absolute;left:625px;top:92px;width:420px;font-size:14.5px;line-height:24px;color:var(--blue-dark)}
.body-copy{font-size:11px;line-height:19.5px;color:#7d8288}
.welcome .body-copy{position:absolute;left:625px;top:152px;width:415px;text-align:justify}
.btn-small{position:absolute;width:96px;height:32px;background:var(--blue-dark);color:#fff;font-size:10px;display:flex;align-items:center;justify-content:center;text-transform:uppercase;gap:4px}
.welcome .btn-small{left:625px;top:274px}

/* steps */
.how-it-works{position:absolute;left:0;top:914px;width:1200px;height:385px;background:var(--blue-light);color:#fff}
.how-it-works .title{position:absolute;left:0;width:1200px;top:40px;text-align:center;font-size:21px;font-weight:600}
.step{position:absolute;top:113px;width:220px;text-align:center}
.step-icon{width:94px;height:94px;margin:0 auto;border-radius:50%;border:4px solid #fff;background:var(--blue-light);display:flex;align-items:center;justify-content:center}
.step-name{margin-top:30px;font-size:13px;font-weight:600;line-height:22px;text-transform:uppercase}
.step-text{margin-top:22px;font-size:11px;line-height:19px;color:#eaf4fb}
.step-arrow{position:absolute;top:118px}

/* reasons */
.reasons{position:absolute;left:0;top:1299px;width:1200px;height:417px;background:var(--paper)}
.reasons .section-heading{position:absolute;left:0;width:1200px;top:34px;text-align:center}
.reason{position:absolute;top:94px;width:273px}
.reason-photo{width:273px;height:151px;border:4px solid #fff;outline:1px solid #d6d9dd}
.reason-title{margin-top:13px;font-size:14px;color:var(--blue-dark)}
.reason .body-copy{margin-top:8px}
.read-more{display:block;margin-top:16px;font-size:10px;font-weight:600;color:var(--blue-dark);text-transform:uppercase}

/* payment */
.payment{position:absolute;left:0;top:1716px;width:1200px;height:273px;background:var(--paper);overflow:hidden}
.card-grid{position:absolute;left:163px;top:50px;display:grid;grid-template-columns:repeat(4,60px);grid-auto-rows:38px;column-gap:8px;row-gap:8px}
.card-tile{background:#fff;border:1px solid #cfd3d8;box-shadow:1px 1px 2px rgba(0,0,0,.15);display:flex;align-items:center;justify-content:center;font-size:8px;font-weight:600;color:var(--blue-deep);text-align:center;line-height:9px;padding:2px}
.payment .section-heading{position:absolute;left:611px;top:42px}
.payment .body-copy{position:absolute;left:611px;top:88px;width:428px;text-align:justify}
.payment .btn-small{left:614px;top:205px}

/* footer */
.site-footer{position:absolute;left:0;top:1989px;width:1200px;height:230px;background:linear-gradient(180deg,var(--blue-light) 0%,#3f8fcc 100%);color:#fff}
.footer-col{position:absolute;top:54px}
.footer-col h4{font-size:14px;font-weight:600;text-transform:uppercase;margin-bottom:9px}
.footer-col p{font-size:11px;line-height:17px;color:#e6f1fa}
.footer-col li{list-style:none;font-size:11px;line-height:23px;color:#e6f1fa}
.footer-link{display:block;margin-top:4px;font-size:10px;font-weight:600;text-transform:uppercase}
.email-field{margin-top:12px;width:240px;height:33px;background:#fff;color:#555;font-size:11px;padding:0 12px;display:flex;align-items:center}
.btn-subscribe{margin-top:12px;width:117px;height:36px;background:var(--blue-dark);font-size:12px;font-weight:700;display:flex;align-items:center;justify-content:center;text-transform:uppercase}
.footer-bar{position:absolute;left:0;top:2219px;width:1200px;height:62px;background:var(--blue-dark);color:#fff;font-size:11px}
.footer-bar .copyright{position:absolute;left:161px;top:23px}
.social{position:absolute;top:17px;width:28px;height:28px;border:1px solid #fff;border-radius:50%}
.footer-bar .code{position:absolute;left:1091px;top:23px;font-size:10px}
</style>
</head>
<body>

<header class="site-header">
  <a class="brand" href="#"><span class="brand-dot"></span>fenwu</a>
  <nav class="main-nav">
    <a class="is-active" href="#" style="left:476px">Home</a>
    <a href="#" style="left:566px">About</a>
    <a href="#" style="left:621px">Send</a>
    <a href="#" style="left:686px">Business</a>
    <a href="#" style="left:774px">Sepa</a>
    <a href="#" style="left:836px">Contact</a>
  </nav>
  <span class="nav-caret"></span>
  <a class="btn-nav btn-login" href="#">LOGIN</a>
  <a class="btn-nav btn-signup" href="#">SIGN UP</a>
</header>

<section class="hero">
  <div class="hero-photo" role="img" aria-label="Photo of a smiling couple at a laptop paying online with a card"></div>
  <span class="slider-arrow" style="left:29px"></span>
  <span class="slider-arrow" style="left:1140px"></span>
  <h1 class="hero-title">New Account-to-Account<br><strong>Payment</strong> Product</h1>
  <p class="hero-text">Lorem ipsum dolor sit amet, consectetur adipiscing elit, sed do eiusmod tempor incididunt ut laborelorem ipmo.</p>
  <a class="btn-primary" href="#">Sign up now</a>
</section>

<section class="welcome">
  <svg class="welcome-shade" width="1200" height="362" aria-hidden="true">
    <polygon points="525,0 1200,0 1200,362 595,362" fill="#f4f5f7"/>
  </svg>
  <div class="welcome-illustration" role="img" aria-label="Illustration of a laptop with payment cards and a mouse"></div>
  <h2 class="section-heading">Welcome to <strong>Fenwu</strong></h2>
  <p class="lead">Lorem ipsum dolor sit amet, consectetur adipiscing elit, sed deiu sm tempor incididunt ut laborelorem ipmo.</p>
  <p class="body-copy">Sed ut perspiciatis unde omnis iste natus error sit voluptatem accusantium dolore mq ue laudantium, totam rem aperiam, eaque ipsa quae ab illo inventore veritatis et quasi archit ecto beatae vitae dicta sunt explicabo. Nemo enim ipsam volupta tem quia volup tas sit aspernatur aut odit aut fugit, sed quia conse quun tur mag ni dolores eos qui rati one voluptatem sequi nesciunt.</p>
  <a class="btn-small" href="#">Read more &raquo;</a>
</section>

<section class="how-it-works">
  <h2 class="title">HOW DOES IT WORK?</h2>

  <svg class="step-arrow" style="left:318px" width="100" height="40" aria-hidden="true"><path d="M4 30 Q50 0 84 22" fill="none" stroke="#7fc0ea" stroke-width="9"/><polygon points="76,10 98,30 72,34" fill="#7fc0ea"/></svg>
  <svg class="step-arrow" style="left:565px;top:138px" width="100" height="40" aria-hidden="true"><path d="M4 24 Q44 40 84 14" fill="none" stroke="#7fc0ea" stroke-width="9"/><polygon points="72,2 98,6 84,28" fill="#7fc0ea"/></svg>
  <svg class="step-arrow" style="left:785px" width="100" height="40" aria-hidden="true"><path d="M4 30 Q50 0 84 22" fill="none" stroke="#7fc0ea" stroke-width="9"/><polygon points="76,10 98,30 72,34" fill="#7fc0ea"/></svg>

  <div class="step" style="left:139px">
    <div class="step-icon"><svg width="40" height="40" viewBox="0 0 40 40" aria-hidden="true"><circle cx="20" cy="11" r="8" fill="#1f5c9f"/><path d="M5 38 Q5 22 20 22 Q35 22 35 38Z" fill="#1f5c9f"/></svg></div>
    <div class="step-name">Our end<br>customers</div>
    <p class="step-text">Sed ut perspiciatis unde otsrs itvoluptatem accusan tium dolore mq ue laudpta te iu dololorlo</p>
  </div>
  <div class="step" style="left:374px">
    <div class="step-icon"><svg width="44" height="36" viewBox="0 0 44 36" aria-hidden="true"><ellipse cx="22" cy="20" rx="17" ry="13" fill="#1f5c9f"/><rect x="11" y="28" width="6" height="7" fill="#1f5c9f"/><rect x="27" y="28" width="6" height="7" fill="#1f5c9f"/><circle cx="22" cy="8" r="6" fill="#1f5c9f" stroke="#4fa3dd" stroke-width="2"/></svg></div>
    <div class="step-name">Merchant<br>partners</div>
    <p class="step-text">Sed ut perspiciatis unde otsrs itvoluptatem accusan tium dolore mq ue laudpta te iu dololorlo</p>
  </div>
  <div class="step" style="left:609px">
    <div class="step-icon"><svg width="44" height="34" viewBox="0 0 44 34" aria-hidden="true"><rect x="8" y="2" width="32" height="20" rx="3" fill="#7fc0ea"/><rect x="3" y="10" width="34" height="22" rx="3" fill="#1f5c9f"/><rect x="3" y="15" width="34" height="4" fill="#fff"/></svg></div>
    <div class="step-name">Credit<br>card network</div>
    <p class="step-text">Sed ut perspiciatis unde otsrs itvoluptatem accusan tium dolore mq ue laudpta te iu dololorlo</p>
  </div>
  <div class="step" style="left:845px">
    <div class="step-icon"><svg width="34" height="40" viewBox="0 0 34 40" aria-hidden="true"><path d="M8 18 V12 a9 9 0 0 1 18 0 V18" fill="none" stroke="#1f5c9f" stroke-width="4"/><rect x="3" y="17" width="28" height="21" rx="3" fill="#1f5c9f"/></svg></div>
    <div class="step-name">Quick,<br>easy checkout</div>
    <p class="step-text">Sed ut perspiciatis unde otsrs itvoluptatem accusan tium dolore mq ue laudpta te iu dololorlo</p>
  </div>
</section>

<section class="reasons">
  <h2 class="section-heading">More reasons to use <strong>Fenwu</strong></h2>
  <article class="reason" style="left:161px">
    <div class="reason-photo" role="img" aria-label="Photo of hands typing on a laptop" style="background:linear-gradient(120deg,#c9dbe9,#e8c9c4 55%,#9aa3ad)"></div>
    <h3 class="reason-title">Lorem ipsum dolor sit amet, conse</h3>
    <p class="body-copy">Sed ut p loerspiciatis unde omnis iste natus error sit volup tatem accusantium dolore mq uloe laud antium, tota m rem aperiam, eaque ipsa quae ab.</p>
    <a class="read-more" href="#">Read more &raquo;</a>
  </article>
  <article class="reason" style="left:464px">
    <div class="reason-photo" role="img" aria-label="Photo of a person holding a smartphone showing a payment confirmation" style="background:linear-gradient(120deg,#b7bcc2,#8a7f78 50%,#dfe3e8)"></div>
    <h3 class="reason-title">Lorem ipsum dolor sit amet, conse</h3>
    <p class="body-copy">Sed ut p loerspiciatis unde omnis iste natus error sit volup tatem accusantium dolore mq uloe laud antium, tota m rem aperiam, eaque ipsa quae ab.</p>
    <a class="read-more" href="#">Read more &raquo;</a>
  </article>
  <article class="reason" style="left:765px">
    <div class="reason-photo" role="img" aria-label="Photo of two phones exchanging a contactless payment" style="background:linear-gradient(120deg,#d9c3c8,#5c6168 45%,#e7b8c4)"></div>
    <h3 class="reason-title">Lorem ipsum dolor sit amet, conse</h3>
    <p class="body-copy">Sed ut p loerspiciatis unde omnis iste natus error sit volup tatem accusantium dolore mq uloe laud antium, tota m rem aperiam, eaque ipsa quae ab.</p>
    <a class="read-more" href="#">Read more &raquo;</a>
  </article>
</section>

<section class="payment">
  <svg class="abs" style="left:0;top:0" width="1200" height="273" aria-hidden="true">
    <rect width="1200" height="273" fill="#f4f5f7"/>
    <polygon points="585,0 1200,0 1200,273 505,273" fill="#ffffff"/>
  </svg>
  <div class="card-grid">
    <span class="card-tile">Zelo</span>
    <span class="card-tile">TrevinCard</span>
    <span class="card-tile">Ambrel Express</span>
    <span class="card-tile">Dalvero</span>
    <span class="card-tile">Ravo</span>
    <span class="card-tile">Pluma</span>
    <span class="card-tile">Tanzo Club</span>
    <span class="card-tile">Kesta</span>
    <span class="card-tile">Norrow Union</span>
    <span class="card-tile">Pennagram</span>
    <span class="card-tile">qCheck</span>
    <span class="card-tile">KRV</span>
    <span class="card-tile">Velmo</span>
    <span class="card-tile">Strano</span>
    <span class="card-tile">Lumpay</span>
  </div>
  <h2 class="section-heading">Account-to-account <strong>Payment</strong></h2>
  <p class="body-copy">Sed ut perspiciatis unde omnis iste natus error sit voluptatem accusantium dolore mq ue laudantium, totam rem aperiam, eaque ipsa quae ab illo inventore veritatis et quasi archit ecto beatae vitae dicta sunt explicabo. Nemo enim ipsam volupta tem quia volup tas sit aspernatur aut odit aut fugit, sed quia conse quun tur mag ni dolores eos qui rati one voluptatem sequi nesciunt.</p>
  <a class="btn-small" href="#">Read more &raquo;</a>
</section>

<footer class="site-footer">
  <div class="footer-col" style="left:161px;width:180px">
    <h4>Fenwu</h4>
    <p>Sed ut perspiciatis unde omnis isten error sit voluptatem accusantiloudo emq ue laudantiu totavoluptatcusa ntiloum dolor emq ue laudn</p>
    <a class="footer-link" href="#">Read more about SEPA</a>
  </div>
  <div class="footer-col" style="left:427px">
    <h4>Resources</h4>
    <ul><li>Support</li><li>Security Center</li><li>Developer Center</li><li>Shopping Carts</li><li>Legal</li></ul>
  </div>
  <div class="footer-col" style="left:611px">
    <h4>Support</h4>
    <ul><li>FAQs</li><li>Privacy Policy</li><li>Recommendations</li><li>Contact</li></ul>
  </div>
  <div class="footer-col" style="left:794px">
    <h4>Sign up newsletter</h4>
    <p>Please sign up here for latest deals</p>
    <div class="email-field">Email address</div>
    <a class="btn-subscribe" href="#">Subscribe</a>
  </div>
</footer>

<div class="footer-bar">
  <span class="copyright">© 2016 Fenwu.&nbsp; All copyrights are reserved&nbsp; Term of Use</span>
  <span class="social" style="left:876px"></span>
  <span class="social" style="left:908px"></span>
  <span class="social" style="left:940px"></span>
  <span class="social" style="left:972px"></span>
  <span class="social" style="left:1004px"></span>
  <span class="code">C4</span>
</div>

</body>
</html>
```